7' x 4' sign for a new multiunit residential mountain location**

Our mission is to build people their dream home through the use of professional and thoughtful design. We're a new developer, building a new and feature-filled fourplex, and need a brand and presence that generates interests and builds our brand. Our homes are professionally and thoughtfully designed - we agonize over the details so our homeowners don't have to once they move in.

We're constructing a new fourplex in downtown Kelowna, BC, Canada. The location is in the heart of the city's entertainment and cultural zones, is surrounded by mountains and a lake, and within an hour of over 100 wineries. "Valley" residents prize their time outdoors - boating, biking, hiking, skiing, and more. It's no wonder Kelowna is often cited as one of the most beautiful and desirable places to live in the world.

attachments - brand elements, rendering of the unit, feature sheet for each unit, and picture of the sign casing (7' wide and 4' long envelop - pic of sign frame attached).

Target Market(s)

Young professionals (age 30 to 45); Empty nestes (age 55+)

Font styles to use
Other font styles liked:
• Cordia New

Requirements
Must have
• Our tag line - Home, by design

Presence - this is an unusual shape and large sign. It must create interest and build our brand.

```html
<!DOCTYPE html>
<html lang="en">
<head>
<meta charset="utf-8">
<title>Fourplex Site Sign – Home, by design</title>
<link rel="stylesheet" href="https://fonts.googleapis.com/css2?family=Barlow+Condensed:wght@300;400;600;700&display=swap">
<style>
  :root {
    --backdrop: #e8eae6;
    --frame-white: #ffffff;
    --brand-maroon: #8b1c34;
    --brand-orange: #f7a935;
    --render-sky: #b9c7dc;
    --render-sky-low: #dfe5ee;
    --render-ground: #4c5158;
    --text-light: #ffffff;
  }
  html, body {
    margin: 0;
    width: 1200px;
    height: 793px;
    overflow: hidden;
    background: var(--backdrop);
  }
  .site-sign {
    position: absolute;
    left: 89px;
    top: 27px;
    width: 1021px;
    height: 738px;
    display: block;
    filter: drop-shadow(0 4px 10px rgba(0,0,0,.18));
  }
  .sign-text { font-family: "Barlow Condensed", sans-serif; }
  .headline-kicker { fill: var(--brand-orange); font-weight: 600; font-size: 64px; }
  .headline-lead { fill: var(--text-light); font-weight: 400; font-size: 64px; }
  .headline-city { fill: var(--brand-orange); font-weight: 700; font-size: 150px; }
  .headline-core { fill: var(--brand-orange); font-weight: 600; font-size: 92px; }
  .tagline { fill: var(--brand-orange); font-size: 76px; }
  .tagline-strong { font-weight: 700; }
  .tagline-soft { font-weight: 300; }
  .lifestyle-copy { fill: var(--text-light); font-weight: 600; font-size: 80px; }
  .feature { fill: var(--brand-maroon); font-weight: 600; font-size: 62px; }
  .feature-note { fill: var(--brand-maroon); font-weight: 300; font-size: 44px; }
</style>
</head>
<body>
<svg class="site-sign" viewBox="0 0 1647 1190" xmlns="http://www.w3.org/2000/svg" aria-label="Fourplex development sign">
  <defs>
    <linearGradient id="render-tones" x1="0" y1="0" x2="0" y2="1">
      <stop offset="0" stop-color="var(--render-sky)"/>
      <stop offset="0.55" stop-color="var(--render-sky-low)"/>
      <stop offset="0.62" stop-color="var(--render-ground)"/>
      <stop offset="1" stop-color="#3b4046"/>
    </linearGradient>
  </defs>

  <polygon class="sign-frame" fill="var(--frame-white)"
    points="0,254 1175,254 1425,0 1647,247 1647,1190 0,1190"/>
  <polygon class="sign-panel" fill="var(--brand-maroon)"
    points="42,294 1192,294 1425,59 1605,267 1605,1152 42,1152"/>

  <path class="rendering-curve" fill="var(--frame-white)"
    d="M42,294 L1072,294 L1018,846 Q560,900 42,680 Z"/>
  <path class="unit-rendering" role="img" aria-label="Architectural rendering of the modern fourplex exterior"
    fill="url(#render-tones)"
    d="M42,294 L1064,294 L1008,834 Q560,884 42,690 Z"/>

  <path class="features-panel" fill="var(--frame-white)"
    d="M967,1152 C990,960 1080,700 1380,636 Q1500,625 1605,657 L1605,1152 Z"/>

  <g class="sign-text" lengthAdjust="spacingAndGlyphs">
    <text class="headline-kicker" x="1272" y="259" textLength="292" lengthAdjust="spacingAndGlyphs">New fourplex</text>
    <text class="headline-lead" x="1272" y="319" textLength="302" lengthAdjust="spacingAndGlyphs">In the heart of</text>
    <text class="headline-city" x="1099" y="429" textLength="500" lengthAdjust="spacingAndGlyphs">Kelowna’s</text>
    <text class="headline-core" x="1104" y="517" textLength="490" lengthAdjust="spacingAndGlyphs">downtown core</text>
    <text class="tagline" x="1155" y="602" textLength="394" lengthAdjust="spacingAndGlyphs"><tspan class="tagline-strong">Home,</tspan><tspan class="tagline-soft"> by design</tspan></text>
  </g>

  <g class="sign-text">
    <text class="lifestyle-copy" x="78" y="954" textLength="824" lengthAdjust="spacingAndGlyphs">"Valley" residents prize their</text>
    <text class="lifestyle-copy" x="78" y="1032" textLength="899" lengthAdjust="spacingAndGlyphs">time outdoors - boating, biking,</text>
    <text class="lifestyle-copy" x="78" y="1105" textLength="736" lengthAdjust="spacingAndGlyphs">hiking, skiing, and more...</text>
  </g>

  <g class="sign-text">
    <text class="feature" x="1214" y="750" textLength="225" lengthAdjust="spacingAndGlyphs">Hot Water</text>
    <text class="feature-note" x="1233" y="792" textLength="185" lengthAdjust="spacingAndGlyphs">on Demand</text>
    <text class="feature" x="1187" y="877" textLength="275" lengthAdjust="spacingAndGlyphs">Solar Ready,</text>
    <text class="feature" x="1060" y="962" textLength="530" lengthAdjust="spacingAndGlyphs">Electric Vehicle plug in,</text>
    <text class="feature" x="1064" y="1047" textLength="523" lengthAdjust="spacingAndGlyphs">Electric Blind Rough in,</text>
    <text class="feature" x="1164" y="1132" textLength="323" lengthAdjust="spacingAndGlyphs">Video Doorbell</text>
  </g>
</svg>
</body>
</html>
```